Letter design, envelope design, and more

Hello, we the Tavrin Gmbh are looking for our shop. Letter C5. Design does not have to be like a business card, so it can have straight lines. Only the color is important. The logo is the text under TaVRin omit.It should not be playful but Profesionel

Font styles to use
Sans Serif

Colors
0555a3
3176b5
85abd2
85cae6
34a7d8
0792cd
cee9f5
cfdfed
000000

Requirements
Must have
• Color like business card, Please, with the text under TaVRin, Correct address Lindmattstr. 4 Zip code 9517 Goldach, as well as Couvert Without addressing only design and logo with TaVrn
Nice to have
• more writing articles
Should not have
• Not too colored, Text under TaVRin, bright colors

```html
<!DOCTYPE html>
<html lang="en">
<head>
<meta charset="utf-8">
<title>Tavrin Gmbh – Letterhead</title>
<link href="https://fonts.googleapis.com/css2?family=Roboto:wght@400;500;900&display=swap" rel="stylesheet">
<style>
  :root {
    --backdrop: #e4e4e4;
    --paper: #f0f0f0;
    --brand-blue: #0555a3;
    --brand-blue-mid: #3176b5;
    --brand-blue-soft: #cfdfed;
    --text: #6e6e70;
    --text-dark: #4a4a4c;
  }
  * { box-sizing: border-box; margin: 0; padding: 0; }
  html, body {
    width: 1200px; height: 1154px; overflow: hidden;
    background: var(--backdrop);
    font-family: "Roboto", Arial, sans-serif;
  }
  .letter {
    position: absolute; left: 208px; top: 27px;
    width: 783px; height: 1100px;
    background: var(--paper);
    color: var(--text);
  }
  .brand {
    position: absolute; left: 69px; top: 112px;
    display: flex; align-items: center; gap: 12px;
  }
  .brand-square { width: 34px; height: 34px; background: var(--brand-blue); }
  .brand-name {
    font-weight: 900; font-size: 32px; letter-spacing: 0.5px;
    color: var(--brand-blue); line-height: 1;
  }
  .contact {
    position: absolute; left: 603px; top: 74px;
    font-size: 13.5px; line-height: 18.7px; color: var(--text-dark);
    font-style: normal;
  }
  .contact .gap { height: 5px; }
  .contact-line { display: flex; align-items: center; gap: 6px; }
  .contact-line svg { width: 12px; height: 12px; flex: none; }
  .recipient {
    position: absolute; left: 69px; top: 330px;
    font-size: 13.6px; line-height: 20.5px;
  }
  .body-copy {
    position: absolute; left: 69px; top: 452px; width: 651px;
    font-size: 13.6px; line-height: 20.5px; text-align: justify;
  }
  .body-copy p + p { margin-top: 41px; }
  .signature {
    position: absolute; left: 69px; top: 747px;
    width: 147px; height: 95px;
    background: linear-gradient(180deg, #e2eaf3, var(--brand-blue-soft));
  }
  .sign-title {
    position: absolute; left: 69px; top: 865px;
    font-size: 13.6px;
  }
  .footer-band {
    position: absolute; left: 0; bottom: 0;
    width: 100%; height: 27px; background: var(--brand-blue);
  }
</style>
</head>
<body>
  <main class="letter">
    <div class="brand">
      <span class="brand-square"></span>
      <span class="brand-name">Tavrin Gmbh</span>
    </div>

    <address class="contact">
      <div>Lindmattstr. 4</div>
      <div>9517 Goldach</div>
      <div class="gap"></div>
      <div class="contact-line">
        <svg viewBox="0 0 24 24"><path fill="#0555a3" d="M6.6 10.8a15.1 15.1 0 0 0 6.6 6.6l2.2-2.2a1 1 0 0 1 1-.25 11.4 11.4 0 0 0 3.6.57 1 1 0 0 1 1 1V20a1 1 0 0 1-1 1A17 17 0 0 1 3 4a1 1 0 0 1 1-1h3.5a1 1 0 0 1 1 1c0 1.25.2 2.45.57 3.57a1 1 0 0 1-.25 1z"/></svg>
        <span>+41 71 555 02 14</span>
      </div>
      <div class="contact-line">
        <svg viewBox="0 0 24 24"><path d="M2 5h20v14H2z M2 5l10 8 10-8" fill="none" stroke="#0555a3" stroke-width="2.4"/></svg>
        <span>info@tavrin.ch</span>
      </div>
      <div class="contact-line">
        <svg viewBox="0 0 24 24"><circle cx="12" cy="12" r="9.5" fill="none" stroke="#0555a3" stroke-width="2"/><path d="M2.5 12h19M12 2.5c-5 5-5 14 0 19M12 2.5c5 5 5 14 0 19" fill="none" stroke="#0555a3" stroke-width="1.6"/></svg>
        <span>www.tavrin.ch</span>
      </div>
    </address>

    <div class="recipient">
      <div>Dear Halvorsen</div>
      <div>Northfield Graphic Link Corporation</div>
      <div>Department Design</div>
    </div>

    <div class="body-copy">
      <p>Lorem ipsum dolor sit amet, consectetuer adipiscing elit. Aenean commodo ligula eget dolor. Aenean massa. Cum sociis natoque penatibus et magnis dis parturient montes, nascetur ridiculus mus. Donec quam felis, ultricies nec, pellentesque eu, pretium quis, sem. Nulla consequat massa quis enim. Donec pede justo, fringilla vel, aliquet nec, vulputate eget, arcu. In enim justo, rhoncus ut, imperdiet a, venenatis vitae, justo. Nullam dictum felis eu pede mollis pretium. Integer tincidunt. Cras dapibus. Vivamus elementum semper nisi.Nullam dictum felis eu pede mollis pretium. Integer tincidunt. Cras dapibus. Vivamus elementum semper nisi.felis eu pede mollis pretium. Integer tincidunt. Cras dapibus.</p>
      <p>Quisque rutrum. Aenean imperdiet. Etiam ultricies nisi vel augue. Curabitur ullamcorper ultricies nisi. Nam eget dui. Etiam rhoncus. Maecenas tempus, tellus eget condimentum rhoncus, sem quam semper libero, sit amet adipiscing sem neque sed ipsum.felis pede mollis pretium. I am tincidunt. Cras dapibus.</p>
    </div>

    <div class="signature" role="img" aria-label="Handwritten signature of the director"></div>
    <div class="sign-title">Director/Excecutive Director</div>

    <div class="footer-band"></div>
  </main>
</body>
</html>
```